Uncoded front page web design for wedding and event planning company

Hi.

I am launching a wedding and event planning company called Silver Fern Celebrations and need a professional and appealing web design.

So, let me explain my company. I am based in Swindon in Wiltshire but the company will plan weddings and events in Oxfordshire, Wiltshire, Berkshire and London.

We will plan weddings, birthdays, conferences, product launches, fashion shows and conventions but the main focus of the website at this stage should be the weddings with all the other occasions being covered under a single 'events' heading.

My contact details for the website should be:
Maureen Hollis
maureen@silverferncelebrations.co.uk
01793 587203 / 07781 452638

I'd like the website to feel clean, bright and elegant and be set against a white or off-white background. My logo is purple and I'd therefore like some purple incorporated into the design although feel free to use a more muted purple as my one might be a little bright? I'm also considering whether it would look nice paired with a little of the colour gold - maybe as a font colour in places?? I'll leave you to figure that one out as your design eye will be better than mine but for your reference below is my purple colour and my suggested gold one....

My purple colour is Pantone 2592 C but feel free to use others
My suggested gold I'm looking at is Pantone 14-1041 TCX

I would like to incorporate a Chatterly feed in the front page if possible, if it looks right. I'd also like to include a variety of pictures as well so I've included a few in a Dropbox folder which is linked below. Please don't feel obliged to use them all by any means (there's loads!) but you've got a few there to play with. If you find any other royalty free images you'd rather use please go ahead but on the understanding I can have them afterwards!

My logo can be retrieved via this Dropbox link...
You'll notice there are 2 styles of placement. Please feel free to use either to fit in with your design...
https://www.filevault.example/sh/kq8pw2mzr4tn7ab/BBBQrt6hNxyvpe5L81GmsWd3Pc?dl=0

The wedding images I have are in this Dropbox folder...
https://www.filevault.example/sh/m9vc2xh6pl1qw8j/BBB4zkrNvLpte6P57YhaJoscb?dl=0

Other than that, it's over to you.... I can't wait to receive your designs :-)

Ooh....finally just to say, as I receive designs in I think I'll notice aspects that I like and don't like and if I feel they'll be useful for other designers, I'll update my brief below. Thanks

BRIEF UPDATE:
Someone asked if I had a tag-line. Could you use "Creating exquisite occasions today for amazing memories tomorrow"

I realise I hadn't explained what I'd like included on my home page so here's some notes to consider....

A welcome to section for me to start narrative about us and our services which has a button that links to our 'about us' page and 'services' page for further information.

A section that nicely illustrates what services we offer whether that be with icons or pictures.

A section with some photos in that would link to our gallery

A section that shows some customer reviews and blog entries that would link to my reviews page and blog to read more.

And finally a contact us section with my details, social media links and site map.

***
I also need to draw attention to where in the UK my services cover. I was therefore thinking perhaps we could use a picture to demonstrate this where it highlights Wiltshire, Oxfordshire, Berkshire and London on a map thereby demonstrating our areas covered. I have found several English county maps when searching on Google but I'm not sure how to highlight the areas I cover (or dull out the areas I don't) so if you have any ideas on this, I'd really like it incorporated. Thanks. (by the way, for those of you not familiar with English counties, the ones I cover are often abbreviated to Wilts, Oxon, Berks, London, so if you find a suitable map with those names on rather than the full names, you'll know what they are!)

I've found an image of the county map which might work well. I was wondering whether we might somehow grey out the counties I don't cover and just keep the ones I do as mentioned above and then crop it into perhaps a shadowed circle? I've attached a screenshot to the brief.

I've decided on the tag-line "Creating exquisite occasions today for amazing memories tomorrow" so if that could be included somewhere that would be great. I also need to draw attention to where in the UK my services cover. I was therefore thinking perhaps we could use a picture to demonstrate this where it highlights Wiltshire, Oxfordshire, Berkshire and London on a map thereby demonstrating our areas covered. I have found several English county maps when searching on Google but I'm not sure how to highlight the areas I cover (or dull out the areas I don't) so if you have any ideas on this, I'd really like it incorporated. Thanks. Added Wednesday, June 24, 2015

Target Market(s)

Predominately women aged 25-55

Industry/Entity Type

Wedding Planner

Number of Pages Required

1 page

Font styles to use
Sans Serif
Script

Requirements
Nice to have
• I'd like to see how the colour theme of purple and perhaps a little gold (maybe as a font colour) look against a white background. I've mentioned the Pantone colours in the brief above.
• I've attached a screenshot of a webpage with gold writing in and fonts that I like. Perhaps it could give you inspiration?
Should not have
• I really don't like the font SCRIPTINA so please done use that.

```html
<!DOCTYPE html>
<html lang="en">
<head>
<meta charset="utf-8">
<title>Silver Fern Celebrations</title>
<link href="https://fonts.googleapis.com/css2?family=Ubuntu:wght@300;400;500;700&family=Open+Sans:wght@400;600&display=swap" rel="stylesheet">
<style>
:root{
  --purple:#8a1b8c;
  --purple-dark:#6d106f;
  --gold:#dbb033;
  --gold-soft:#e2b63a;
  --page:#efece8;
  --panel:#ffffff;
  --card:#f5f5f5;
  --ink:#222222;
  --text:#555555;
  --muted:#888888;
  --line:#e3e3e3;
  --footer:#262626;
  --footer-text:#b8b8b8;
}
*{box-sizing:border-box;margin:0;padding:0}
html,body{width:1200px;height:2490px;overflow:hidden}
body{position:relative;background:var(--page);font-family:"Open Sans",Arial,sans-serif;color:var(--text)}
.abs{position:absolute}
a{color:inherit;text-decoration:none}

/* header */
.site-header{left:0;top:0;width:1200px;height:148px;background:#fff;border-bottom:1px solid #ddd}
.contact-bar{left:631px;top:0;width:470px;height:38px;background:var(--gold);border-radius:0 0 4px 4px;color:#fff;font-size:13px;display:flex;align-items:center;justify-content:center;gap:34px}
.contact-bar span{display:flex;align-items:center;gap:7px}
.brand{left:100px;top:28px;display:flex;align-items:center;gap:10px;font-family:"Ubuntu",sans-serif;font-weight:400;color:var(--purple);font-size:22px;line-height:1.1}
.brand-dot{width:44px;height:44px;border-radius:50%;background:var(--purple);flex:none}
.main-nav{left:503px;top:70px;display:flex}
.nav-item{width:129px;padding-left:20px;border-left:1px solid #e6e6e6;font-family:"Ubuntu",sans-serif}
.nav-item:first-child{border-left:none}
.nav-item b{display:block;color:var(--purple);font-weight:400;font-size:14px}
.nav-item small{display:block;color:#444;font-size:11.5px;margin-top:7px}

/* hero */
.hero{left:0;top:149px;width:1200px;height:606px;background:linear-gradient(90deg,#8f8f8f 0%,#b4b4b2 35%,#c4c3c0 60%,#a9a8a6 100%)}
.hero-photo{left:560px;top:149px;width:540px;height:606px;background:radial-gradient(ellipse at 50% 40%,#d9c2b4 0%,#a89a92 45%,rgba(40,40,40,.55) 80%,rgba(0,0,0,0) 100%)}
.hero-title{left:128px;top:300px;font-family:"Ubuntu",sans-serif;color:#fff;text-shadow:0 2px 4px rgba(0,0,0,.35)}
.hero-title h1{font-size:60px;font-weight:700;line-height:1}
.hero-title h2{font-size:38px;font-weight:400;line-height:1.1;margin-top:6px}
.hero-copy{left:130px;top:422px;width:420px;color:#fff;font-size:14px;line-height:24px}
.btn-start{left:125px;top:510px;width:194px;height:44px;background:var(--purple);border:2px solid #d8a6d8;border-radius:4px;color:#fff;font-family:"Ubuntu",sans-serif;font-size:15px;display:flex;align-items:center;justify-content:center;gap:12px}
.slider-arrow{top:467px;width:34px;height:34px;border-radius:50%;background:rgba(60,60,60,.55);display:flex;align-items:center;justify-content:center}
.lace{height:22px;width:1200px;left:0;background:linear-gradient(#f7f6f4,#e9e7e3)}

/* services */
.services{left:100px;top:689px;width:1000px;height:424px;background:var(--card)}
.service{top:0;height:424px;width:333px;text-align:center}
.service.featured{background:#fff;box-shadow:0 0 8px rgba(0,0,0,.25);height:426px;top:-2px;z-index:2}
.service-img{position:absolute;left:21px;top:22px;width:288px;height:199px}
.service h3{position:absolute;left:0;width:100%;top:240px;font-family:"Ubuntu",sans-serif;font-weight:400;font-size:15px;color:var(--ink)}
.service p{position:absolute;left:30px;width:273px;top:276px;font-size:11.5px;line-height:20px}
.read-more{position:absolute;left:100px;width:133px;top:352px;height:40px;border-top:1px solid var(--line);border-bottom:1px solid var(--line);font-family:"Ubuntu",sans-serif;font-size:13px;color:#333;display:flex;align-items:center;justify-content:center;gap:7px}

/* welcome */
.welcome{left:100px;top:1172px;width:1000px;text-align:center}
.welcome h2{font-family:"Ubuntu",sans-serif;font-weight:400;font-size:32px;color:var(--ink)}
.welcome h2 span{color:var(--purple)}
.welcome p{margin:14px auto 0;width:960px;font-size:12px;line-height:21px}

/* main panel */
.panel{left:100px;top:1350px;width:1000px;height:775px;background:var(--panel);border-top:3px solid var(--gold)}
.panel-head{left:100px;top:1353px;width:1000px;height:62px;background:#f8f8f8;border-bottom:1px solid var(--line);font-family:"Ubuntu",sans-serif;font-size:26px;color:var(--ink);padding:16px 0 0 25px}
.event{top:1461px;width:470px;height:186px}
.event-img{position:absolute;left:0;top:0;width:162px;height:186px}
.pager{position:absolute;left:162px;top:0;width:33px;height:186px;border:1px solid var(--line);background:#fff;font-size:13px;color:#999;text-align:center}
.pager div{height:34px;line-height:34px;border-bottom:1px solid var(--line)}
.pager .active{background:var(--gold);color:#fff}
.pager .chev{height:24px;line-height:24px;display:flex;align-items:center;justify-content:center}
.event h4{position:absolute;left:219px;top:0;font-family:"Ubuntu",sans-serif;font-weight:400;font-size:16px;color:#333}
.event time{position:absolute;left:219px;top:30px;font-size:12.5px;color:var(--purple);display:flex;align-items:center;gap:6px}
.event p{position:absolute;left:219px;top:56px;width:240px;font-size:11.5px;line-height:22px}
.divider{left:100px;top:1698px;width:1000px;height:1px;background:var(--line)}
.gallery-title{left:125px;top:1728px;font-family:"Ubuntu",sans-serif;font-weight:300;font-size:31px;color:var(--ink)}
.dots{left:694px;top:1743px;display:flex;gap:5px}
.dots i{width:17px;height:17px;border-radius:50%;border:1.5px solid #333;display:block}
.dots i.on{background:#222}
.gallery-item{top:1786px;width:209px}
.gallery-img{position:relative;height:201px}
.gallery-icons{position:absolute;left:64px;top:96px;display:flex;gap:10px}
.gallery-icons span{width:35px;height:35px;border-radius:50%;background:rgba(50,50,50,.75);display:flex;align-items:center;justify-content:center}
.gallery-cap{height:51px;background:var(--gold);color:#fff;font-family:"Ubuntu",sans-serif;font-size:15px;display:flex;align-items:center;justify-content:center}
.gallery-item p{font-size:11.5px;line-height:20px;margin-top:12px}
.social-box{left:812px;top:1740px;width:259px;height:338px;border:1px solid var(--line);background:#fff}
.social-box h5{font-family:"Ubuntu",sans-serif;font-weight:400;font-size:15px;color:#222;padding:16px 0 0 15px;height:52px;border-bottom:1px solid var(--line)}
.social-name{position:absolute;left:22px;top:72px;display:flex;align-items:center;gap:6px;font-family:"Ubuntu",sans-serif;color:var(--purple);font-size:12px;width:100px;line-height:1.2}
.social-name i{width:18px;height:18px;border-radius:50%;background:var(--purple);flex:none}
.social-count{position:absolute;left:128px;top:80px;font-size:12px;color:#333}
.like-btn{position:absolute;left:128px;top:100px;width:40px;height:16px;background:#5b74a8}
.avatars{position:absolute;left:22px;top:136px;width:216px;display:grid;grid-template-columns:repeat(4,50px);gap:6px 5px}
.avatars span{height:48px;background:linear-gradient(135deg,#7d7d7d,#c9c2bb)}
.social-foot{position:absolute;left:22px;right:22px;top:292px;border-top:1px solid var(--line);padding-top:12px;font-size:12px;color:#333;display:flex;align-items:center;gap:12px}
.social-foot i{width:9px;height:11px;background:#3b5998;display:block}

/* footer */
.site-footer{left:0;top:2171px;width:1200px;height:256px;background:var(--footer)}
.foot-col{top:2213px;color:var(--footer-text);font-size:12px}
.foot-col h6{font-family:"Ubuntu",sans-serif;font-weight:400;font-size:15px;color:#fff;margin-bottom:20px}
.foot-col li{list-style:none;line-height:24px}
.news-text{width:228px;line-height:20px;font-size:11.5px;color:#999}
.field{width:220px;height:40px;background:#fff;color:#333;font-size:12px;padding:12px 14px}
.news-row{display:flex;margin-top:16px}
.btn-sub{width:97px;height:40px;background:var(--purple);color:#fff;font-size:12.5px;display:flex;align-items:center;justify-content:center}
.contact-line{display:flex;align-items:center;gap:14px;margin-top:14px}
.foot-brand{left:908px;top:2258px;display:flex;align-items:center;gap:10px;font-family:"Ubuntu",sans-serif;color:#fff;font-size:24px;line-height:1.1}
.foot-brand i{width:40px;height:40px;border-radius:50%;background:#fff;flex:none}
.bottom-bar{left:0;top:2427px;width:1200px;height:63px;background:var(--purple);color:#fff;font-size:13px}
.copyright{position:absolute;left:100px;top:22px}
.social-icons{position:absolute;left:946px;top:15px;display:flex;gap:7px}
.social-icons span{width:28px;height:28px;border-radius:50%;border:1.5px solid #fff;display:block}
</style>
</head>
<body>

<header class="site-header abs">
  <div class="contact-bar abs">
    <span><svg width="12" height="12" viewBox="0 0 24 24"><path fill="#fff" d="M6.6 10.8a15 15 0 0 0 6.6 6.6l2.2-2.2a1 1 0 0 1 1-.25 11.4 11.4 0 0 0 3.6.57 1 1 0 0 1 1 1V20a1 1 0 0 1-1 1A17 17 0 0 1 3 4a1 1 0 0 1 1-1h3.5a1 1 0 0 1 1 1c0 1.25.2 2.45.57 3.57a1 1 0 0 1-.25 1z"/></svg>01793 587203 / 07781 452638</span>
    <span><svg width="13" height="11" viewBox="0 0 24 18"><rect x="1" y="1" width="22" height="16" fill="none" stroke="#fff" stroke-width="2"/><path d="M1 1l11 9 11-9" fill="none" stroke="#fff" stroke-width="2"/></svg>maureen@silverferncelebrations.co.uk</span>
  </div>
  <div class="brand abs"><i class="brand-dot"></i><span>Silver Fern<br>Celebrations</span></div>
  <nav class="main-nav abs">
    <a class="nav-item"><b>HOME</b><small>Start here</small></a>
    <a class="nav-item"><b>WEDDINGS</b><small>Who we are</small></a>
    <a class="nav-item"><b>EVENTS</b><small>Programms</small></a>
    <a class="nav-item"><b>GALLERY</b><small>See our photos</small></a>
    <a class="nav-item"><b>CONTACT US</b><small>Get in touch</small></a>
  </nav>
</header>

<section class="hero abs"></section>
<div class="hero-photo abs" role="img" aria-label="Bride and groom portrait with a bouquet of purple flowers"></div>
<div class="hero-title abs"><h1>SILVER FERN</h1><h2>CELEBRATIONS</h2></div>
<p class="hero-copy abs">We are wedding and event planning company.<br>We will plan weddings, birthdays, conferences, product launches, fashion shows and conventions</p>
<a class="btn-start abs">GETTING STARTED <svg width="14" height="14" viewBox="0 0 16 16"><circle cx="8" cy="8" r="8" fill="#fff"/><path d="M6.5 4.5 10 8l-3.5 3.5" fill="none" stroke="#8a1b8c" stroke-width="2"/></svg></a>
<span class="slider-arrow abs" style="left:38px"><svg width="10" height="14" viewBox="0 0 10 14"><path d="M8 1 2 7l6 6" fill="none" stroke="#fff" stroke-width="2"/></svg></span>
<span class="slider-arrow abs" style="left:1133px"><svg width="10" height="14" viewBox="0 0 10 14"><path d="m2 1 6 6-6 6" fill="none" stroke="#fff" stroke-width="2"/></svg></span>
<div class="lace abs" style="top:755px" role="img" aria-label="Lace border trim"></div>

<section class="services abs">
  <article class="service abs" style="left:0">
    <div class="service-img" role="img" aria-label="Couple dancing at a wedding reception" style="background:linear-gradient(135deg,#7a5b45,#d6c3b0 55%,#5a4637)"></div>
    <h3>WEDDINGS</h3>
    <p>Lorem ipsum dolor sit amet, consec teer adipiscing. Prsent vestibulum molestie la my hendrerit. mauris hasellllus. Porta. Lorem ipsum dolor</p>
    <a class="read-more">READ MORE <svg width="12" height="12" viewBox="0 0 16 16"><circle cx="8" cy="8" r="8" fill="#333"/><path d="M6.5 4.5 10 8l-3.5 3.5" fill="none" stroke="#fff" stroke-width="2"/></svg></a>
  </article>
  <article class="service featured abs" style="left:333px">
    <div class="service-img" role="img" aria-label="Models walking a fashion show runway" style="background:linear-gradient(180deg,#e8e8e8,#b5aca2 60%,#6f6a65)"></div>
    <h3>FASHION SHOWS</h3>
    <p>Lorem ipsum dolor sit amet, consec teer adipiscing. Prsent vestibulum molestie la my hendrerit. mauris hasellllus. Porta. Lorem ipsum dolor</p>
    <a class="read-more">READ MORE <svg width="12" height="12" viewBox="0 0 16 16"><circle cx="8" cy="8" r="8" fill="#333"/><path d="M6.5 4.5 10 8l-3.5 3.5" fill="none" stroke="#fff" stroke-width="2"/></svg></a>
  </article>
  <article class="service abs" style="left:667px">
    <div class="service-img" role="img" aria-label="Speaker presenting to a conference audience" style="background:linear-gradient(135deg,#c96a2e,#3d4a7a 55%,#1c2340)"></div>
    <h3>CONFERENCES</h3>
    <p>Lorem ipsum dolor sit amet, consec teer adipiscing. Prsent vestibulum molestie la my hendrerit. mauris hasellllus. Porta. Lorem ipsum dolor</p>
    <a class="read-more">READ MORE <svg width="12" height="12" viewBox="0 0 16 16"><circle cx="8" cy="8" r="8" fill="#333"/><path d="M6.5 4.5 10 8l-3.5 3.5" fill="none" stroke="#fff" stroke-width="2"/></svg></a>
  </article>
</section>

<section class="welcome abs">
  <h2>Welcome To <span>Silver Fern Celebrations</span></h2>
  <p>Lorem ipsum dolor sit amet, consectetur adipiscing elit, sed do eiusmod tempor incididunt ut labore et dolore magna aliqua. Ut enim ad minim veniam, quis nostrud exercitation ullamco laboris nisi ut aliquip ex ea commodo consequat. Duis aute irure dolor in reprehenderit in voluptate velit esse cillum dolore eu fugiat nulla pariatur. Excepteur sint occaecat cupidatat non proident, sunt in culpa qui officia deserunt mollit anim id est laborum</p>
</section>

<section class="panel abs"></section>
<h3 class="panel-head abs" style="font-weight:400">Feature Events</h3>

<article class="event abs" style="left:125px">
  <div class="event-img" role="img" aria-label="Bride and groom dancing under lights" style="background:linear-gradient(135deg,#3a2a3a,#d8d0d0 50%,#6a4a5a)"></div>
  <div class="pager">
    <div class="chev"><svg width="10" height="6" viewBox="0 0 10 6"><path d="M1 5 5 1l4 4" fill="none" stroke="#222" stroke-width="1.6"/></svg></div>
    <div class="active">01</div><div>02</div><div>03</div><div>04</div>
    <div class="chev" style="border-bottom:none"><svg width="10" height="6" viewBox="0 0 10 6"><path d="m1 1 4 4 4-4" fill="none" stroke="#222" stroke-width="1.6"/></svg></div>
  </div>
  <h4>Nemo Enim Ipsam Voluptatem</h4>
  <time><svg width="11" height="11" viewBox="0 0 12 12"><circle cx="6" cy="6" r="5" fill="none" stroke="#8a1b8c" stroke-width="1.5"/><path d="M6 3v3l2 1.5" fill="none" stroke="#8a1b8c" stroke-width="1.3"/></svg>19.00 PM - 21.00 PM</time>
  <p>Lorem ipsum dolor sit amet, consectetur adipiscing elit, sed do eiusmod tempor incididunt ut labore et dolore magna aliqua. Ut enim ad minim veniam, quis nostrud exercitation ullamco laboris nisi ut aliquip ex ea commodo consequat.</p>
</article>
<article class="event abs" style="left:631px">
  <div class="event-img" role="img" aria-label="Bride signing the wedding register" style="background:linear-gradient(135deg,#2c3a55,#e8e2dc 55%,#a8b89a)"></div>
  <div class="pager">
    <div class="chev"><svg width="10" height="6" viewBox="0 0 10 6"><path d="M1 5 5 1l4 4" fill="none" stroke="#222" stroke-width="1.6"/></svg></div>
    <div class="active">01</div><div>02</div><div>03</div><div>04</div>
    <div class="chev" style="border-bottom:none"><svg width="10" height="6" viewBox="0 0 10 6"><path d="m1 1 4 4 4-4" fill="none" stroke="#222" stroke-width="1.6"/></svg></div>
  </div>
  <h4>Nemo Enim Ipsam Voluptatem</h4>
  <time><svg width="11" height="11" viewBox="0 0 12 12"><circle cx="6" cy="6" r="5" fill="none" stroke="#8a1b8c" stroke-width="1.5"/><path d="M6 3v3l2 1.5" fill="none" stroke="#8a1b8c" stroke-width="1.3"/></svg>19.00 PM - 21.00 PM</time>
  <p>Lorem ipsum dolor sit amet, consectetur adipiscing elit, sed do eiusmod tempor incididunt ut labore et dolore magna aliqua. Ut enim ad minim veniam, quis nostrud exercitation ullamco laboris nisi ut aliquip ex ea commodo consequat.</p>
</article>

<div class="divider abs"></div>
<h3 class="gallery-title abs" style="font-weight:300">Our Gallery</h3>
<div class="dots abs"><i class="on"></i><i></i><i></i><i></i></div>

<figure class="gallery-item abs" style="left:125px">
  <div class="gallery-img" role="img" aria-label="Vintage wedding car decorated with ribbons" style="background:linear-gradient(180deg,#4d6a2a,#c9b8c4 55%,#e9e4e6)">
    <div class="gallery-icons"><span><svg width="14" height="14" viewBox="0 0 14 14"><circle cx="6" cy="6" r="4" fill="none" stroke="#fff" stroke-width="1.8"/><path d="m9 9 4 4" stroke="#fff" stroke-width="1.8"/></svg></span><span><svg width="14" height="14" viewBox="0 0 14 14"><path d="M5 9 9 5M6 3.5l1.5-1.5a2.5 2.5 0 0 1 3.5 3.5L9.5 7M8 10.5 6.5 12A2.5 2.5 0 0 1 3 8.5L4.5 7" fill="none" stroke="#fff" stroke-width="1.6"/></svg></span></div>
  </div>
  <figcaption class="gallery-cap">Velit sit amet bibendum</figcaption>
  <p>Lorem ipsum dolor sit amet, consectetur adipiscing elit, sed do eiusmod</p>
</figure>
<figure class="gallery-item abs" style="left:349px">
  <div class="gallery-img" role="img" aria-label="Waiter serving plated wedding dinner" style="background:linear-gradient(135deg,#9a8a7a,#f1ede8 50%,#c8b49a)">
    <div class="gallery-icons"><span><svg width="14" height="14" viewBox="0 0 14 14"><circle cx="6" cy="6" r="4" fill="none" stroke="#fff" stroke-width="1.8"/><path d="m9 9 4 4" stroke="#fff" stroke-width="1.8"/></svg></span><span><svg width="14" height="14" viewBox="0 0 14 14"><path d="M5 9 9 5M6 3.5l1.5-1.5a2.5 2.5 0 0 1 3.5 3.5L9.5 7M8 10.5 6.5 12A2.5 2.5 0 0 1 3 8.5L4.5 7" fill="none" stroke="#fff" stroke-width="1.6"/></svg></span></div>
  </div>
  <figcaption class="gallery-cap">Velit sit amet bibendum</figcaption>
  <p>Lorem ipsum dolor sit amet, consectetur adipiscing elit, sed do eiusmod</p>
</figure>
<figure class="gallery-item abs" style="left:571px">
  <div class="gallery-img" role="img" aria-label="Church aisle decorated for a wedding ceremony" style="background:linear-gradient(180deg,#6a4a32,#b08a62 45%,#e6e2dc)">
    <div class="gallery-icons"><span><svg width="14" height="14" viewBox="0 0 14 14"><circle cx="6" cy="6" r="4" fill="none" stroke="#fff" stroke-width="1.8"/><path d="m9 9 4 4" stroke="#fff" stroke-width="1.8"/></svg></span><span><svg width="14" height="14" viewBox="0 0 14 14"><path d="M5 9 9 5M6 3.5l1.5-1.5a2.5 2.5 0 0 1 3.5 3.5L9.5 7M8 10.5 6.5 12A2.5 2.5 0 0 1 3 8.5L4.5 7" fill="none" stroke="#fff" stroke-width="1.6"/></svg></span></div>
  </div>
  <figcaption class="gallery-cap">Velit sit amet bibendum</figcaption>
  <p>Lorem ipsum dolor sit amet, consectetur adipiscing elit, sed do eiusmod</p>
</figure>

<aside class="social-box abs">
  <h5>Follow Us On Chatterly</h5>
  <div class="social-name"><i></i><span>Silver Fern Celebrations</span></div>
  <div class="social-count">37,845 people like</div>
  <span class="like-btn"></span>
  <div class="avatars" role="img" aria-label="Grid of follower profile photos">
    <span></span><span></span><span></span><span></span><span></span><span></span><span></span><span></span>
  </div>
  <div class="social-foot"><i></i>Chatterly social plugin</div>
</aside>

<div class="lace abs" style="top:2150px;height:21px;background:linear-gradient(#dedbd6,#c9c6c1)" role="img" aria-label="Lace border trim"></div>

<footer class="site-footer abs"></footer>
<div class="foot-col abs" style="left:100px">
  <h6>QUICK LINKS</h6>
  <ul><li>Home</li><li>Weddings</li><li>Events</li><li>Gallery</li><li>Contact Us</li></ul>
</div>
<div class="foot-col abs" style="left:302px">
  <h6>SIGN UP FOR NEWSLETTER</h6>
  <p class="news-text">Excepteur sint occaecat cupidatat non proident, sunt in culpa qui</p>
  <div class="field" style="margin-top:16px;width:220px">Enter Name</div>
  <div class="news-row"><div class="field" style="width:123px">Enter Email</div><a class="btn-sub">SUBSCRIBE</a></div>
</div>
<div class="foot-col abs" style="left:611px;color:#999">
  <h6>CONTACT US</h6>
  <p style="line-height:20px">Silver Fern Celebrations<br>4821 KL&nbsp; Lindenveld The Netherlands</p>
  <div class="contact-line" style="margin-top:22px"><svg width="16" height="16" viewBox="0 0 24 24"><path fill="none" stroke="#ccc" stroke-width="1.8" d="M6.6 10.8a15 15 0 0 0 6.6 6.6l2.2-2.2a1 1 0 0 1 1-.25 11.4 11.4 0 0 0 3.6.57 1 1 0 0 1 1 1V20a1 1 0 0 1-1 1A17 17 0 0 1 3 4a1 1 0 0 1 1-1h3.5a1 1 0 0 1 1 1c0 1.25.2 2.45.57 3.57a1 1 0 0 1-.25 1z"/></svg>+1 01793 587203 / 07781 452638</div>
  <div class="contact-line"><svg width="16" height="12" viewBox="0 0 24 18"><rect x="1" y="1" width="22" height="16" fill="none" stroke="#ccc" stroke-width="2"/><path d="M1 1l11 9 11-9" fill="none" stroke="#ccc" stroke-width="2"/></svg>maureen@silverferncelebrations.co.uk</div>
</div>
<div class="foot-brand abs"><i></i><span>Silver Fern<br>Celebrations</span></div>

<div class="bottom-bar abs">
  <span class="copyright">Copyright©2015 Silver Fern Celebrations</span>
  <div class="social-icons"><span></span><span></span><span></span><span></span><span></span></div>
</div>

</body>
</html>
```